design a construction company business card

Design business card around our logo. Card must have all the typical info: name, title, address, phone, email, business name, etc. Somewhere on the card I would like to see our motto "Built on integrity... Inspired by commitment." Consider adding a splash of bright orange to the card to complement the blues and silvers/grays in the logo. We are open to metallic inks, textures, etc. We would like to see options on both light and dark backgrounds. The font in the logo is Euro Technic Extended Regular.

```html
<!DOCTYPE html>
<html lang="en">
<head>
<meta charset="utf-8">
<title>Halden Contracting – Business Card</title>
<link rel="stylesheet" href="https://fonts.googleapis.com/css2?family=Roboto:wght@400;500&display=swap">
<style>
  :root {
    --backdrop: #1c1c1c;
    --card: #0b0b0b;
    --silver: #e4e4e4;
    --silver-dim: #bdbdbd;
  }
  html, body {
    margin: 0;
    padding: 0;
    width: 1200px;
    height: 913px;
    overflow: hidden;
    background: var(--backdrop);
  }
  .canvas {
    width: 1200px;
    height: 913px;
    display: flex;
    align-items: center;
    justify-content: center;
    gap: 60px;
  }
  .card {
    width: 520px;
    height: 297px;
    background: var(--card);
    border-radius: 3px;
    box-shadow: 0 14px 30px rgba(0,0,0,0.5);
    box-sizing: border-box;
    display: flex;
    flex-direction: column;
    align-items: center;
    justify-content: center;
    color: var(--silver);
    font-family: "Roboto", sans-serif;
  }
  .brand-name {
    font-size: 30px;
    font-weight: 500;
    letter-spacing: 1px;
    color: var(--silver);
    display: flex;
    align-items: center;
    gap: 14px;
    margin: 0;
  }
  .brand-mark {
    width: 20px;
    height: 20px;
    background: var(--silver);
  }
  .card-back {
    justify-content: flex-start;
    padding-top: 62px;
  }
  .back-brand {
    font-size: 15px;
    font-weight: 500;
    letter-spacing: 1px;
    color: var(--silver);
    margin: 0 0 24px;
  }
  .person-name {
    font-size: 18px;
    font-weight: 500;
    letter-spacing: 0.5px;
    margin: 0;
  }
  .person-title {
    font-size: 12px;
    letter-spacing: 0.5px;
    color: var(--silver-dim);
    margin: 3px 0 26px;
  }
  .contact {
    font-size: 11.5px;
    letter-spacing: 0.4px;
    line-height: 1.75;
    text-align: center;
    color: var(--silver);
    margin: 0;
  }
  .motto {
    font-size: 12.5px;
    margin-top: 8px;
  }
</style>
</head>
<body>
<main class="canvas">
  <section class="card card-front">
    <p class="brand-name"><span class="brand-mark"></span>Halden Contracting, Inc.</p>
  </section>

  <section class="card card-back">
    <p class="back-brand">Halden Contracting, Inc.</p>
    <h1 class="person-name">MARTIN COLE</h1>
    <p class="person-title">PRESIDENT</p>
    <p class="contact">
      418 BIRCHWOOD LANE, JUNEAU, ALASKA 34581<br>
      555-019-4827 &nbsp;|&nbsp; MCOLE@HALDEN.COM &nbsp;|&nbsp; WWW.HALDEN.COM
    </p>
    <p class="contact motto">Built on integrity... Inspired by commitment.</p>
  </section>
</main>
</body>
</html>
```